Wordpress theme website for professionals working together

My partner and I are offering business services, my wife in the energy business as mainly as member of the board of commissioners. I am working as interim manager/consultant in the accounting and finance area. Both activities are connected in one company VELMOT BV (dutch ltd). We need a CV based website. Beside this we do some financial and accounting services.

Target Market(s)

small medium business

Font styles to use
Sans Serif

Colors

Designer to choose colors to be used in the design.

Requirements
Must have
• Pictures of both members.
• CLEAN AND SIMPLE
• I LIKE BLACK & WHITE
Nice to have
• I like design like this theme: http://theme.pruxelo-example.com/resume/

```html
<!DOCTYPE html>
<html lang="en">
<head>
<meta charset="utf-8">
<title>Velmot BV – Pieter &amp; Ingrid</title>
<link rel="stylesheet" href="https://fonts.googleapis.com/css2?family=Montserrat:wght@400;600;700&family=Open+Sans:wght@400;600&display=swap">
<style>
:root{
  --ink:#111;
  --dark:#1b1b1b;
  --dark-2:#262626;
  --mid:#6d6d6d;
  --light:#e9e9e9;
  --paper:#fff;
  --accent:#1e4f94;
  --bar-bg:#c9c9c9;
}
*{box-sizing:border-box;margin:0;padding:0}
html,body{width:1200px;height:5248px;overflow:hidden}
body{font-family:"Open Sans",Arial,sans-serif;color:var(--ink);background:var(--paper);font-size:12px;line-height:1.7}
.section{position:relative;width:1200px;overflow:hidden}
.abs{position:absolute}
h1,h2,h3,h4,.nav,.btn{font-family:"Montserrat",Arial,sans-serif}
.title{position:absolute;left:0;width:1200px;text-align:center;font-size:26px;font-weight:700;letter-spacing:1px}
.title::after{content:"";display:block;width:40px;height:2px;background:currentColor;margin:10px auto 0;opacity:.5}
.intro{position:absolute;left:320px;width:560px;text-align:center;font-size:11px;line-height:1.6}

.site-header{height:63px;background:var(--paper)}
.brand{left:172px;top:16px;font-family:"Montserrat",sans-serif;font-weight:700;font-size:26px;color:var(--accent);display:flex;align-items:center;gap:8px}
.brand .mark{width:14px;height:14px;background:var(--accent)}
.nav{right:172px;top:24px;display:flex;gap:22px;font-size:10px;letter-spacing:1px;color:#444}
.nav .on{color:var(--ink);font-weight:600}

.hero{height:560px;background:linear-gradient(90deg,#efefef,#d8d8d8)}
.portrait{right:0;top:0;width:560px;height:100%;background:linear-gradient(120deg,#d2d2d2 0%,#9a9a9a 45%,#3a3a3a 100%)}
.person-name{left:172px;font-size:44px;font-weight:400;letter-spacing:4px}
.person-text{left:172px;width:400px;font-size:12px;line-height:1.75;color:#222}
.signature{left:172px;width:120px;height:40px;background:linear-gradient(90deg,#bcbcbc,#d6d6d6)}

.experience{height:665px;background:linear-gradient(180deg,#1f1f1f,#141414);color:#fff}
.timeline-line{left:599px;top:147px;width:2px;height:455px;background:#444}
.node{left:580px;width:40px;height:40px;border-radius:50%;background:#222;border:2px solid #555}
.end-node{left:592px;top:596px;width:16px;height:16px;border-radius:50%;background:#555}
.tag{background:#f2f2f2;color:var(--ink);font-size:12px;font-weight:600;padding:7px 18px;font-family:"Montserrat",sans-serif}
.tag.left{right:645px}
.tag.right{left:645px}
.exp-text{width:330px;font-size:11px;line-height:1.55;color:#ddd}
.exp-text.left{right:645px;text-align:right}
.exp-text.right{left:660px}

.jobs{height:532px;background:var(--paper)}
.col-head{font-size:15px;font-weight:700;letter-spacing:.5px}
.job-title{font-family:"Montserrat",sans-serif;font-weight:700;font-size:14px;line-height:1.3;width:140px}
.job-text{width:210px;font-size:10.5px;line-height:1.55}
.job-line{width:1px;background:#bbb}
.job-dot{width:10px;height:10px;border-radius:50%;border:1px solid #999;background:#fff}

.skills{height:553px;background:var(--light)}
.skill-label{font-family:"Montserrat",sans-serif;font-size:11px;font-weight:700;letter-spacing:.3px}
.bar{height:24px;background:var(--bar-bg);display:flex}
.bar .fill{background:var(--ink);height:100%}
.pct{position:absolute;top:0;height:24px;width:62px;background:#a9a9a9;font-size:10px;line-height:24px;padding-left:10px;clip-path:polygon(0 0,80% 0,100% 50%,80% 100%,0 100%)}

.facts{height:437px;background:linear-gradient(135deg,#161616,#0c0c0c)}
.fact{top:98px;width:276px;height:234px;background:var(--dark-2);color:#fff;text-align:center}
.fact svg{margin-top:40px}
.fact h3{font-size:13px;font-weight:700;letter-spacing:1px;margin-top:18px}
.fact p{font-size:12px;color:#ccc;line-height:1.5;margin-top:4px}

.portfolio{height:753px;background:var(--paper)}
.shot{width:276px}

.profile-2{height:434px;background:linear-gradient(90deg,#e3e3e3,#cfcfcf)}
.btn{display:inline-block;background:var(--ink);color:#fff;font-size:10px;font-weight:600;letter-spacing:1px;padding:10px 20px}
.pointer{left:582px;bottom:-1px;width:0;height:0;border-left:18px solid transparent;border-right:18px solid transparent;border-bottom:18px solid var(--paper)}

.contact{height:563px;background:var(--paper)}
.info h4{font-size:15px;font-weight:600;display:flex;align-items:center;gap:10px}
.info p{font-size:10.5px;line-height:1.55;color:#444;padding-left:26px}
.field{left:543px;width:409px;height:30px;border:1px solid #ccc;font-size:10px;color:#666;padding:7px 10px}
.field.msg{height:130px}

.office{height:393px;background:linear-gradient(100deg,#2b6fc4 0%,#4a8ad6 40%,#7a5443 60%,#4b2f25 100%)}
.office h2{left:172px;top:215px;color:#fff;font-size:40px;font-weight:700;line-height:1.05;letter-spacing:1px}

.site-footer{height:295px;background:var(--dark);color:#fff}
.foot-col h4{font-size:15px;font-weight:600;margin-bottom:10px}
.foot-col li{list-style:none;font-size:10px;color:#aaa;line-height:1.75}
.news-input{left:707px;top:90px;width:230px;height:30px;background:#fff}
.news-btn{left:937px;top:90px;width:92px;height:30px;background:#111;border:1px solid #444;font-size:10px;text-align:center;line-height:28px;font-family:"Montserrat",sans-serif;font-weight:600}
.social{left:707px;top:148px;display:flex;gap:22px}
.social span{width:16px;height:16px;border-radius:50%;background:#fff;display:block}
.foot-rule{left:172px;top:227px;width:857px;height:1px;background:#333}
.copyright{left:0;width:1200px;top:250px;text-align:center;font-size:10px;color:#999}
</style>
</head>
<body>

<header class="section site-header">
  <div class="abs brand"><span class="mark"></span>Velmot</div>
  <nav class="abs nav"><span class="on">HOME</span><span>INGRID</span><span>SKILLS</span><span>EXPERIENCE</span><span>PORTFOLIO</span><span>EDUCATION</span><span>CONTACT</span></nav>
</header>

<section class="section hero">
  <div class="abs portrait" role="img" aria-label="Black and white portrait photo of Pieter"></div>
  <h1 class="abs person-name" style="top:140px">PIETER</h1>
  <p class="abs person-text" style="top:205px">Sed ut perspiciatis unde omnis iste natus error sit voluptatem accusantium doloremque laudantium, totam rem aperiam, eaque ipsa quae ab illo inventore veritatis et quasi architecto beatae vitae dicta sunt explicabo. Nemo enim ipsam voluptatem quia voluptas sit aspernatur aut odit aut fugit, sed quia consequuntur magni dolores eos qui ratione voluptatem sequi nesciunt. Neque porro quisquam est, qui dolorem ipsum quia dolor sit amet, consectetur.</p>
  <div class="abs signature" style="top:380px" role="img" aria-label="Handwritten signature of Pieter"></div>
</section>

<section class="section experience">
  <h2 class="title" style="top:62px;color:#fff">EXPERIENCE</h2>
  <div class="abs timeline-line"></div>

  <div class="abs node" style="top:155px"></div>
  <div class="abs tag left" style="top:162px">Accounting 2012</div>
  <p class="abs exp-text right" style="top:148px">Sed ut perspiciatis unde omnis iste natus error sit voluptatem accusantium doloremque laudantium, totam rem et perspiciatis unde omnis iste natus error sit voluptatem.</p>

  <div class="abs node" style="top:242px"></div>
  <p class="abs exp-text left" style="top:232px">Sed ut perspiciatis unde omnis iste natus error sit voluptatem accusantium doloremque laudantium, totam rem aperiam sed ut perspiciatis unde omnis iste natus error sit voluptatem.</p>
  <div class="abs tag right" style="top:249px">Team player 2013</div>

  <div class="abs node" style="top:333px"></div>
  <div class="abs tag left" style="top:340px">Trouble shooter 2014</div>
  <p class="abs exp-text right" style="top:325px">Sed ut perspiciatis unde omnis iste natus error sit voluptatem accusantium doloremque laudantium, totam rem et perspiciatis unde omnis iste natus error sit voluptatem.</p>

  <div class="abs node" style="top:417px"></div>
  <p class="abs exp-text left" style="top:405px">Sed ut perspiciatis unde omnis iste natus error sit voluptatem accusantium doloremque laudantium, totam rem aperiam sed ut perspiciatis unde omnis iste natus error sit voluptatem.</p>
  <div class="abs tag right" style="top:424px">Project management 2016</div>

  <div class="abs node" style="top:505px"></div>
  <div class="abs tag left" style="top:512px">Financial Reporter 2016</div>
  <p class="abs exp-text right" style="top:497px">Sed ut perspiciatis unde omnis iste natus error sit voluptatem accusantium doloremque laudantium, totam rem et perspiciatis unde omnis iste natus error sit voluptatem.</p>

  <div class="abs end-node"></div>
</section>

<section class="section jobs">
  <h2 class="title" style="top:62px">PIETER <span style="font-weight:400">JOBS</span></h2>

  <h3 class="abs col-head" style="left:172px;top:140px">ACTUAL JOBS</h3>
  <div class="abs job-line" style="left:325px;top:195px;height:300px"></div>
  <div class="abs job-title" style="left:172px;top:225px">Advisor WRX</div>
  <div class="abs job-dot" style="left:320px;top:228px"></div>
  <p class="abs job-text" style="left:350px;top:213px">Sed ut perspiciatis unde omnis iste natus error sit voluptatem accusantium doloremque laudantium, totam rem.</p>
  <div class="abs job-title" style="left:172px;top:304px">Advisor How &amp; knower</div>
  <div class="abs job-dot" style="left:320px;top:318px"></div>
  <p class="abs job-text" style="left:350px;top:300px">Sed ut perspiciatis unde omnis iste natus error sit voluptatem accusantium doloremque laudantium, totam rem.</p>
  <p class="abs job-text" style="left:350px;top:395px">Sed ut perspiciatis unde omnis iste natus error sit voluptatem accusantium doloremque laudantium, totam rem sed ut perspiciatis unde omnis iste natus error sit voluptatem.</p>

  <h3 class="abs col-head" style="left:632px;top:140px">FINISHED JOBS</h3>
  <div class="abs job-line" style="left:788px;top:195px;height:300px"></div>
  <div class="abs job-title" style="left:632px;top:212px">Controller a.i. WRX</div>
  <div class="abs job-dot" style="left:783px;top:226px"></div>
  <p class="abs job-text" style="left:812px;top:210px">Sed ut perspiciatis unde omnis iste natus error sit voluptatem accusantium doloremque laudantium, totam rem.</p>
  <div class="abs job-title" style="left:632px;top:303px">Advisor Ovelia Green</div>
  <div class="abs job-dot" style="left:783px;top:318px"></div>
  <p class="abs job-text" style="left:812px;top:300px">Sed ut perspiciatis unde omnis iste natus error sit voluptatem accusantium doloremque laudantium, totam rem.</p>
  <div class="abs job-title" style="left:632px;top:400px">Financial director EVQ</div>
  <div class="abs job-dot" style="left:783px;top:414px"></div>
  <p class="abs job-text" style="left:812px;top:392px">Sed ut perspiciatis unde omnis iste natus error sit voluptatem accusantium doloremque laudantium, totam rem.</p>
</section>

<section class="section skills">
  <h2 class="title" style="top:55px">SKILLS</h2>
  <p class="intro" style="top:118px">Sed ut perspiciatis unde omnis iste natus error sit voluptatem accusantium doloremque laudantium, totam rem aperiam sed ut perspiciatis unde omnis iste natus error sit voluptatem accusantium doloremque laudantium.</p>

  <div class="abs skill-label" style="left:172px;top:183px">ANNUAL REPORTING</div>
  <div class="abs bar" style="left:172px;top:203px;width:353px"><div class="fill" style="width:80%"></div></div>
  <div class="pct" style="left:460px;top:203px">80%</div>
  <div class="abs skill-label" style="left:172px;top:253px">FINANCIAL MONTHLY REPORTING</div>
  <div class="abs bar" style="left:172px;top:273px;width:353px"><div class="fill" style="width:66%"></div></div>
  <div class="pct" style="left:460px;top:273px">40%</div>
  <div class="abs skill-label" style="left:172px;top:323px">ACCOUNTING</div>
  <div class="abs bar" style="left:172px;top:343px;width:353px"><div class="fill" style="width:90%"></div></div>
  <div class="pct" style="left:490px;top:343px">90%</div>
  <div class="abs skill-label" style="left:172px;top:393px">FINANCIAL MANAGEMENT</div>
  <div class="abs bar" style="left:172px;top:413px;width:353px"><div class="fill" style="width:70%"></div></div>
  <div class="pct" style="left:460px;top:413px">75%</div>

  <div class="abs skill-label" style="left:640px;top:183px">PROJECT MANAGEMENT</div>
  <div class="abs bar" style="left:640px;top:203px;width:382px"><div class="fill" style="width:75%"></div></div>
  <div class="pct" style="left:935px;top:203px">75%</div>
  <div class="abs skill-label" style="left:640px;top:253px">TEAM PLAYER</div>
  <div class="abs bar" style="left:640px;top:273px;width:382px"><div class="fill" style="width:80%"></div></div>
  <div class="pct" style="left:940px;top:273px">80%</div>
  <div class="abs skill-label" style="left:640px;top:323px">TROUBLE SHOOTER</div>
  <div class="abs bar" style="left:640px;top:343px;width:382px"><div class="fill" style="width:80%"></div></div>
  <div class="pct" style="left:940px;top:343px">85%</div>
  <div class="abs skill-label" style="left:640px;top:393px">ETC</div>
  <div class="abs bar" style="left:640px;top:413px;width:382px"><div class="fill" style="width:30%"></div></div>
  <div class="pct" style="left:940px;top:413px">30%</div>
</section>

<section class="section facts">
  <div class="abs fact" style="left:172px">
    <svg width="56" height="48" viewBox="0 0 56 48" fill="none" stroke="#fff" stroke-width="2"><path d="M28 8 C20 3 10 3 3 6 V42 C10 39 20 39 28 44 C36 39 46 39 53 42 V6 C46 3 36 3 28 8 Z"/><path d="M28 8 V44"/></svg>
    <h3>EDUCATION</h3>
    <p>Norva (RA)<br>Lyceum B</p>
  </div>
  <div class="abs fact" style="left:462px">
    <svg width="52" height="52" viewBox="0 0 52 52" fill="none" stroke="#fff" stroke-width="2"><path d="M6 46 L30 22"/><path d="M30 22 a10 10 0 1 0 8 -14 l-6 6 -4 -2 -2 -4 6 -6"/><path d="M46 46 L20 20"/><path d="M20 20 L12 12 L8 4 L4 8 L12 12"/></svg>
    <h3>WORKED FOR</h3>
    <p>Strand Advocaten &amp; Notarissen<br>Kelderman Audit</p>
  </div>
  <div class="abs fact" style="left:753px">
    <svg width="54" height="44" viewBox="0 0 54 44" fill="none" stroke="#fff" stroke-width="2"><rect x="2" y="2" width="50" height="40"/><path d="M6 36 L20 20 L30 30 L38 22 L48 36"/><circle cx="38" cy="12" r="4"/></svg>
    <h3>OTHER</h3>
    <p>Fotography</p>
  </div>
</section>

<section class="section portfolio">
  <h2 class="title" style="top:62px">PORTFOLIO</h2>
  <p class="intro" style="top:118px">Sed ut perspiciatis unde omnis iste natus error sit voluptatem accusantium doloremque laudantium, totam rem aperiam sed ut perspiciatis unde omnis iste natus error sit voluptatem accusantium doloremque laudantium.</p>
  <div class="abs shot" style="left:172px;top:193px;height:231px;background:linear-gradient(135deg,#e6e3dd,#6b5a4a)" role="img" aria-label="Photo of hands working on financial documents with a coffee cup"></div>
  <div class="abs shot" style="left:462px;top:193px;height:231px;background:linear-gradient(135deg,#2a4d7a,#8fb2d6)" role="img" aria-label="Photo of a rising business chart in blue tones"></div>
  <div class="abs shot" style="left:753px;top:193px;height:231px;background:linear-gradient(135deg,#c9c9c9,#5c5c5c)" role="img" aria-label="Photo of a laptop with a financial report"></div>
  <div class="abs shot" style="left:172px;top:435px;height:227px;background:linear-gradient(135deg,#4f6f94,#d9dde2)" role="img" aria-label="Photo of a calculator and charts on a desk"></div>
  <div class="abs shot" style="left:462px;top:435px;height:227px;background:linear-gradient(135deg,#f2f0ec,#8a7a6a)" role="img" aria-label="Photo of hands typing on a laptop"></div>
  <div class="abs shot" style="left:753px;top:435px;height:227px;background:linear-gradient(135deg,#e5e8ec,#4a5f78)" role="img" aria-label="Photo of business people meeting at a laptop"></div>
</section>

<section class="section profile-2">
  <div class="abs portrait" role="img" aria-label="Black and white portrait photo of Ingrid"></div>
  <h2 class="abs person-name" style="top:75px">INGRID</h2>
  <p class="abs person-text" style="top:137px">Sed ut perspiciatis unde omnis iste natus error sit voluptatem accusantium doloremque laudantium, totam rem aperiam, eaque ipsa quae ab illo inventore veritatis et quasi architecto beatae vitae dicta sunt explicabo. Nemo enim ipsam voluptatem quia voluptas sit aspernatur aut odit aut fugit, sed quia consequuntur magni dolores eos qui ratione voluptatem sequi nesciunt. Neque porro quisquam est, qui dolorem ipsum quia dolor sit amet, consectetur.</p>
  <span class="abs btn" style="left:172px;top:330px">VIEW PROFILE</span>
  <div class="abs pointer"></div>
</section>

<section class="section contact">
  <h2 class="title" style="top:62px">CONTACT</h2>
  <p class="intro" style="top:118px">Sed ut perspiciatis unde omnis iste natus error sit voluptatem accusantium doloremque laudantium, totam rem aperiam sed ut perspiciatis unde omnis iste natus error sit voluptatem accusantium doloremque laudantium.</p>

  <div class="abs info" style="left:265px;top:205px">
    <h4><svg width="16" height="18" viewBox="0 0 16 18" fill="none" stroke="#333" stroke-width="1.5"><path d="M8 17 C3 11 2 9 2 6.5 a6 6 0 0 1 12 0 C14 9 13 11 8 17Z"/><circle cx="8" cy="6.5" r="2"/></svg>Address</h4>
    <p>VELMOT BV<br>Lorem ipsum core dummy<br>Dummy lo quim 0770 dumm<br>9876 ZM Dummy NL</p>
  </div>
  <div class="abs info" style="left:265px;top:340px">
    <h4><svg width="16" height="12" viewBox="0 0 16 12" fill="none" stroke="#333" stroke-width="1.5"><rect x="1" y="1" width="14" height="10"/><path d="M1 1 L8 7 L15 1"/></svg>Email</h4>
    <p>info@velmot-example.com</p>
  </div>
  <div class="abs info" style="left:265px;top:410px">
    <h4><svg width="16" height="16" viewBox="0 0 16 16" fill="none" stroke="#333" stroke-width="1.5"><path d="M3 1 L6 1 L7 5 L5 6.5 C6 9 7 10 9.5 11 L11 9 L15 10 L15 13 C15 14 14 15 13 15 C6 15 1 10 1 3 C1 2 2 1 3 1Z"/></svg>Phone</h4>
    <p>(0)10 555 0142, (0)10 555 0143</p>
  </div>

  <div class="abs field" style="top:210px">Name</div>
  <div class="abs field" style="top:250px">Email</div>
  <div class="abs field" style="top:288px">Phone</div>
  <div class="abs field msg" style="top:326px">Message</div>
  <span class="abs btn" style="left:543px;top:474px">SUBMIT HERE</span>
</section>

<section class="section office" role="img" aria-label="Photo of the brick office building against a blue sky">
  <h2 class="abs">OUR<br>OFFICE</h2>
</section>

<footer class="section site-footer">
  <div class="abs foot-col" style="left:172px;top:40px"><h4>Company</h4><ul><li>Sed ut perspiciatis</li><li>Unde omnis iste</li><li>Voluptatem</li><li>Accusantium</li><li>Doloremque</li><li>Laudantium</li></ul></div>
  <div class="abs foot-col" style="left:353px;top:40px"><h4>About</h4><ul><li>Sed ut perspiciatis</li><li>Unde omnis iste</li><li>Voluptatem</li><li>Accusantium</li><li>Doloremque</li><li>Laudantium</li></ul></div>
  <div class="abs foot-col" style="left:518px;top:40px"><h4>Links</h4><ul><li>Sed ut perspiciatis</li><li>Unde omnis iste</li><li>Voluptatem</li><li>Accusantium</li><li>Doloremque</li><li>Laudantium</li></ul></div>
  <div class="abs foot-col" style="left:707px;top:40px"><h4>Newsletter</h4></div>
  <div class="abs news-input"></div>
  <div class="abs news-btn">SIGN UP</div>
  <div class="abs social" aria-label="Social media links"><span></span><span></span><span></span><span></span></div>
  <div class="abs foot-rule"></div>
  <p class="abs copyright">© 2016 All Rights Are Reserved Terms of Use | Privacy Policy</p>
</footer>

</body>
</html>
```